Harborline Auto LLC

Car Dealer Customer Service
Address: 2874 Cresthaven Road, Shelbyville, TN 37162
web: www.harborlineautoxq.net
email: harborlineautoxq@mailnest.example
Phone: (931) 555-0148
Phone: (629) 555-0173

```html
<!DOCTYPE html>
<html lang="en">
<head>
<meta charset="utf-8">
<title>Harborline Auto LLC – Business Card</title>
<link href="https://fonts.googleapis.com/css2?family=Montserrat:wght@400;500;700;800&display=swap" rel="stylesheet">
<style>
  :root {
    --brand-blue: #1d7aad;
    --wave-blue: #2a95cf;
    --wave-light: #4aa8db;
    --accent-gold: #ecb444;
    --ink: #1b1b1b;
    --paper: #ffffff;
    --stage: #e9ebee;
  }
  * { box-sizing: border-box; margin: 0; padding: 0; }
  html, body { width: 1200px; height: 887px; overflow: hidden; }
  body {
    background: var(--stage);
    font-family: "Montserrat", Arial, sans-serif;
    display: flex; flex-direction: column; align-items: center; justify-content: center;
    gap: 28px;
  }
  .card {
    position: relative;
    width: 720px; height: 411px;
    border-radius: 30px;
    overflow: hidden;
    box-shadow: 0 6px 18px rgba(0,0,0,.15);
  }
  /* back side */
  .card--back { background: var(--brand-blue); }
  .card--back .wordmark {
    position: absolute; left: 0; right: 0; top: 0; bottom: 0;
    display: flex; flex-direction: column; align-items: center; justify-content: center; gap: 22px;
  }
  .wordmark__dot { width: 110px; height: 110px; border-radius: 50%; background: var(--paper); }
  .card--back .wordmark__name {
    color: var(--paper); font-weight: 800; font-size: 46px; letter-spacing: 1px; text-transform: uppercase;
  }
  /* front side */
  .card--front { background: var(--paper); }
  .card--front .wave { position: absolute; left: 0; top: 0; width: 720px; height: 411px; }
  .card--front .wordmark {
    position: absolute; left: 30px; top: 70px; width: 320px;
    display: flex; flex-direction: column; align-items: center; gap: 18px;
  }
  .card--front .wordmark__dot { width: 92px; height: 92px; background: var(--wave-blue); }
  .card--front .wordmark__name {
    color: var(--brand-blue); font-weight: 800; font-size: 30px; letter-spacing: .5px; text-transform: uppercase;
  }
  .divider {
    position: absolute; left: 372px; top: 58px; width: 2px; height: 200px; background: var(--wave-blue);
  }
  .contact { position: absolute; left: 394px; top: 52px; color: var(--ink); font-size: 14.5px; }
  .contact__role { font-size: 15px; margin-bottom: 10px; }
  .contact__address { line-height: 1.35; margin-bottom: 10px; padding-left: 14px; }
  .contact__list { list-style: none; }
  .contact__item { display: flex; align-items: center; gap: 8px; line-height: 1.55; }
  .contact__item svg { width: 16px; height: 16px; flex: none; fill: var(--wave-blue); }
  .contact__domain { color: var(--wave-blue); }
</style>
</head>
<body>

  <section class="card card--back" aria-label="Card back">
    <div class="wordmark">
      <span class="wordmark__dot"></span>
      <span class="wordmark__name">Harborline Auto</span>
    </div>
  </section>

  <section class="card card--front" aria-label="Card front">
    <svg class="wave" viewBox="0 0 720 411" aria-hidden="true">
      <defs>
        <linearGradient id="waveFill" x1="0" y1="1" x2="1" y2="0">
          <stop offset="0" stop-color="var(--wave-light)"/>
          <stop offset="1" stop-color="var(--wave-blue)"/>
        </linearGradient>
      </defs>
      <path d="M0 360 C 170 395, 330 395, 470 340 S 650 290, 720 282 L720 411 L0 411 Z" fill="url(#waveFill)"/>
      <path d="M120 386 C 280 392, 380 370, 470 325 S 610 275, 700 268" fill="none" stroke="var(--accent-gold)" stroke-width="4" stroke-linecap="round"/>
    </svg>

    <div class="wordmark">
      <span class="wordmark__dot"></span>
      <span class="wordmark__name">Harborline Auto</span>
    </div>

    <div class="divider"></div>

    <div class="contact">
      <p class="contact__role">Car Dealer Customer Service</p>
      <p class="contact__address">2874 Cresthaven Road,<br>Shelbyville, TN 37162</p>
      <ul class="contact__list">
        <li class="contact__item">
          <svg viewBox="0 0 24 24"><path d="M6.6 10.8a15 15 0 0 0 6.6 6.6l2.2-2.2c.3-.3.7-.4 1-.2 1.1.4 2.3.6 3.6.6.6 0 1 .4 1 1V20c0 .6-.4 1-1 1A17 17 0 0 1 3 4c0-.6.4-1 1-1h3.5c.6 0 1 .4 1 1 0 1.3.2 2.5.6 3.6.1.3 0 .7-.2 1z"/></svg>
          (931) 555-0148
        </li>
        <li class="contact__item">
          <svg viewBox="0 0 24 24"><path d="M3 8c0-2 4-4 9-4s9 2 9 4v2h-5V8H8v2H3zM5 12h14l1 8H4zm7 2a2.5 2.5 0 1 0 0 5 2.5 2.5 0 0 0 0-5z"/></svg>
          (629) 555-0173
        </li>
        <li class="contact__item">
          <svg viewBox="0 0 24 24"><path d="M2 5h20v14H2zm2 2v.5l8 5.5 8-5.5V7z"/></svg>
          harborlineautoxq@mailnest.example
        </li>
        <li class="contact__item">
          <svg viewBox="0 0 24 24"><circle cx="12" cy="12" r="10"/></svg>
          <span>www.<span class="contact__domain">harborlineautoxq</span>.net</span>
        </li>
      </ul>
    </div>
  </section>

</body>
</html>
```